Irrigation Business needs their business cards modernised and revamped

I would like to keep my current logo, colours and revamp the format of the card.

I would like the card to be clean yet important.

Im not sure if you include texture but i would like the named logo to be indented into the card etc.

show me something alive and free something thats clinical to the point yet has a feel of achievement. i would like people to go nice card.

Target Market(s)

high end clients, corporate, sports field manger, the guys that make the decisions

Industry/Entity Type

Business

Contact Information for Business Card

nformation to be included

Dean Harlow (Director)
0487305526
dean@kolvat.biz
www.kestonfieldworks.com

instagram logo
google logo
facebook logo

Colors

Designer to choose colors to be used in the design.

Requirements
Nice to have
• indentations a really nice feel to the card good texture

```html
<!DOCTYPE html>
<html lang="en">
<head>
<meta charset="utf-8">
<title>Keston Fieldworks — Business Card</title>
<link rel="stylesheet" href="https://fonts.googleapis.com/css2?family=Open+Sans:wght@400;600;700&display=swap">
<style>
  :root {
    --backdrop: #3a3230;
    --card: #141516;
    --card-edge: #1d1e20;
    --silver: #9a9c9f;
    --silver-dark: #6f7174;
    --blue-light: #36a9d8;
    --blue-mid: #3f7cc4;
    --blue-name: #3b8fd6;
    --green-title: #3cb878;
    --divider: #4a4c4f;
    --ink: #f2f3f4;
  }
  * { margin: 0; padding: 0; box-sizing: border-box; }
  html, body {
    width: 1200px; height: 864px; overflow: hidden;
    background: var(--backdrop);
    font-family: "Open Sans", Arial, sans-serif;
  }
  .sheet {
    width: 1200px; height: 864px;
    display: flex; align-items: center; justify-content: center; gap: 60px;
  }
  .card {
    width: 540px; height: 309px;
    background: var(--card);
    border: 1px solid var(--card-edge);
    box-shadow: 0 18px 40px rgba(0,0,0,.45);
    position: relative;
  }
  /* Front */
  .card-front {
    display: flex; flex-direction: column; align-items: center; justify-content: center;
  }
  .brand-dot {
    width: 80px; height: 80px; border-radius: 50%;
    background: var(--silver-dark);
    margin-bottom: 16px;
  }
  .brand-name {
    font-weight: 700; font-size: 28px; letter-spacing: 1px;
    color: var(--silver); text-transform: uppercase;
  }
  .social-row { display: flex; gap: 8px; margin-top: 18px; }
  .social-dot {
    width: 20px; height: 20px; border-radius: 50%;
    background: var(--silver-dark);
  }
  /* Back */
  .card-back { display: flex; align-items: center; padding: 0 40px; }
  .mark-block {
    width: 190px; display: flex; flex-direction: column; align-items: center;
  }
  .mark-circle {
    width: 110px; height: 110px; border-radius: 50%;
    background: var(--blue-mid);
    margin-bottom: 14px;
  }
  .mark-name {
    font-weight: 700; font-size: 14px; color: var(--blue-light);
    text-transform: uppercase; letter-spacing: .5px; white-space: nowrap;
  }
  .divider {
    width: 1px; height: 150px; background: var(--divider); margin: 0 26px 0 22px;
  }
  .details { color: var(--ink); }
  .person-name { font-weight: 700; font-size: 17px; color: var(--blue-name); text-transform: uppercase; line-height: 1.1; }
  .person-title { font-weight: 600; font-size: 16px; color: var(--green-title); text-transform: uppercase; margin-bottom: 12px; }
  .contact-list { list-style: none; }
  .contact-list li { display: flex; align-items: center; gap: 8px; font-size: 15px; line-height: 1.45; white-space: nowrap; }
  .contact-list svg { width: 13px; height: 13px; flex: none; fill: var(--blue-mid); }
</style>
</head>
<body>
  <main class="sheet">
    <section class="card card-front" aria-label="Card front">
      <div class="brand-dot"></div>
      <div class="brand-name">Keston Fieldworks</div>
      <div class="social-row">
        <span class="social-dot" aria-label="Social profile"></span>
        <span class="social-dot" aria-label="Social profile"></span>
        <span class="social-dot" aria-label="Social profile"></span>
      </div>
    </section>

    <section class="card card-back" aria-label="Card back">
      <div class="mark-block">
        <div class="mark-circle"></div>
        <div class="mark-name">Keston Fieldworks</div>
      </div>
      <div class="divider"></div>
      <div class="details">
        <div class="person-name">Dean Harlow</div>
        <div class="person-title">Director</div>
        <ul class="contact-list">
          <li>
            <svg viewBox="0 0 16 16" aria-hidden="true"><path d="M3.5 1.5l2.5 0 1 3.5-1.6 1.2c.8 1.8 2.2 3.2 4 4l1.2-1.6 3.5 1v2.5c0 .8-.7 1.4-1.5 1.4C6.8 13.5 2.5 9.2 2 3c0-.8.7-1.5 1.5-1.5z"/></svg>
            0487305526
          </li>
          <li>
            <svg viewBox="0 0 16 16" aria-hidden="true"><path d="M1 3h14v10H1z M1.5 3.5L8 9l6.5-5.5" stroke="#141516" stroke-width="1.2"/></svg>
            dean@kolvat.biz
          </li>
          <li>
            <svg viewBox="0 0 16 16" aria-hidden="true"><circle cx="8" cy="8" r="7"/><path d="M1 8h14M8 1c2.5 2.5 2.5 11.5 0 14M8 1c-2.5 2.5-2.5 11.5 0 14" stroke="#141516" stroke-width="1" fill="none"/></svg>
            www.kestonfieldworks.com
          </li>
        </ul>
      </div>
    </section>
  </main>
</body>
</html>
```